Create a wordpress website for Tovarin business solution

This project is to create a complete website with all pages.

Overview
The purpose of this project is to create a full complete website with all pages (16 pages). The site should be professional and modern. The site is for an IT recruiting and IT training company. The site needs to be easy to administer and update content. It should be simple to add pages, videos and testimonials later. I will leave the site layout, color schemes and flow to the designers.

Navigation Menu (Home, who we are, what we do, what makes us different, why it matters, candidate portal, contact us, Blog)

WHO WE ARE should be a drop down menu with link to pages (about us, mission, vision and purpose, our team)

WHAT WE DO should be drop down menu with link to the following pages (IT Recruiting, IT Training, Hardware and software sales)

What makes us different should be single page with different paragraph titles. (We live what we do, we don't compromise quality, we share knowledge, staffing guarantee)

Why it matters should be single page with paragraph titles. (Quickly fill positions, candidate career development)

Candidate portal should links to my portal login page. I can add the correct URL later. I just need it to link to somewhere. I can change it.

Contact us should have (address, phone number, google map and a form to submit request for a call back)

Blog - This link should launch a wordpress blogging module

Target Market(s)

IT RECRUITING AND CONSULTING

Industry/Entity Type

It Company

Coding

Coded - Design and coding required

Requirements
Must have
• Company Logo
• Navigation Menu (Home, who we are, what we do, what makes us different, why it matters, candidate portal, contact us)
• WHO WE ARE should be a drop down menu with link to pages (about us, mission, vision and purpose, our team)
• WHAT WE DO should be drop down menu with link to the following pages (IT Recruiting, IT Training, Hardware and software sales)
• What makes us different should be single page with different paragraph titles. (We live what we do, we don't compromise quality, we share knowledge, staffing guarantee)
• Why it matters should be single page with paragraph titles. (Quickly fill positions, candidate career development)
• Candidate portal should links to my portal login page. I can add the correct URL later. I just need it to link to somewhere. I can change it.
• Contact us should have (address, phone number, google map and a form to submit request for a call back)

```html
<!DOCTYPE html>
<html lang="en">
<head>
<meta charset="utf-8">
<title>Tovarin Business Solution</title>
<link rel="stylesheet" href="https://fonts.googleapis.com/css2?family=Open+Sans:wght@400;600;700&family=Roboto+Condensed:wght@400;700&display=swap">
<style>
:root{
  --orange:#ef7f1a;
  --orange-dark:#d96c0c;
  --blue:#0d5aa7;
  --blue-dark:#0a4a8c;
  --ink:#222;
  --text:#6b6b6b;
  --light:#f1f1f1;
  --line:#d6d6d6;
  --white:#fff;
  --dark:#1c1c1c;
}
*{box-sizing:border-box;margin:0;padding:0}
html,body{width:1200px;height:3543px;overflow:hidden}
body{font-family:"Open Sans",Arial,sans-serif;color:var(--text);background:var(--white);position:relative}
.section{position:absolute;left:0;width:1200px;overflow:hidden}
.abs{position:absolute}
.head-font{font-family:"Roboto Condensed","Arial Narrow",sans-serif}

/* top bar */
.topbar{top:0;height:40px;background:var(--orange)}
.social-dot{position:absolute;top:10px;width:20px;height:20px;border-radius:50%;background:rgba(255,255,255,.9)}
.login{right:78px;top:9px;color:var(--white);font-size:15px}
/* header */
.header{top:40px;height:85px;background:var(--white)}
.brand{left:78px;top:14px;display:flex;align-items:center;gap:12px}
.brand-mark{width:22px;height:22px;background:var(--orange)}
.brand-name{font-family:"Roboto Condensed",sans-serif;font-weight:700;font-size:34px;color:var(--blue);letter-spacing:.5px;line-height:1}
.brand-sub{left:112px;top:60px;font-size:12px;color:var(--blue);font-weight:700;letter-spacing:2px}
.call{left:784px;top:24px;color:var(--orange);font-size:24px;font-family:"Roboto Condensed",sans-serif}
.call-icon{left:912px;top:17px;width:50px;height:50px;border-radius:50%;border:2px solid var(--line)}
.call-number{left:973px;top:20px;color:var(--blue);font-size:30px;font-weight:700;font-family:"Roboto Condensed",sans-serif}
/* nav */
.nav{top:125px;height:59px;background:var(--blue)}
.nav ul{list-style:none;display:flex;position:absolute;left:78px;top:0;height:59px}
.nav li{color:var(--white);font-family:"Roboto Condensed",sans-serif;font-size:17px;text-transform:uppercase;line-height:59px;padding:0 14px}
.nav li.active{background:var(--orange);padding:0 22px}
/* hero */
.hero{top:184px;height:572px}
.hero-photo{position:absolute;inset:0;background:linear-gradient(100deg,#8a857c 0%,#b7b1a6 30%,#d9d6d0 60%,#9c9a96 100%)}
.hero-title{left:78px;top:172px;color:var(--white);font-size:52px;font-weight:700;font-family:"Roboto Condensed",sans-serif}
.hero-sub{left:78px;top:245px;color:var(--white);font-size:22px}
.btn-white{background:var(--white);color:var(--orange);font-weight:700;font-size:17px;text-transform:uppercase;display:flex;align-items:center;justify-content:center;border-radius:3px}
.hero-btn{left:78px;top:307px;width:201px;height:52px}
/* section titles */
.title{width:1200px;left:0;text-align:center;font-family:"Roboto Condensed",sans-serif;font-size:46px;text-transform:uppercase;color:var(--blue)}
.title .accent{color:var(--orange)}
.lead{text-align:center;font-size:15px;line-height:1.6}
/* welcome */
.welcome{top:756px;height:352px}
.welcome .title{top:44px}
.welcome .lead{left:130px;width:945px;top:121px}
.btn-blue{background:var(--blue);color:var(--white);font-size:17px;text-transform:uppercase;display:flex;align-items:center;justify-content:center;gap:8px;border-radius:2px}
.welcome-btn{left:515px;top:250px;width:170px;height:48px}
/* about / mission */
.about{top:1108px;height:357px}
.about-left{left:0;top:0;width:598px;height:357px;background:linear-gradient(120deg,var(--orange) 0%,#f29a4a 55%,var(--orange-dark) 100%)}
.about-right{left:602px;top:0;width:598px;height:357px;background:var(--blue)}
.dash-v{left:598px;top:0;width:4px;height:357px;border-left:4px dashed var(--white)}
.dash-h{left:0;top:353px;width:1200px;height:4px;border-top:4px dashed var(--white)}
.about h2{font-family:"Roboto Condensed",sans-serif;font-weight:400;color:var(--white)}
.about-title{left:78px;top:50px;font-size:46px;text-transform:uppercase}
.about-text{left:78px;top:116px;width:500px;color:var(--white);font-size:15px;line-height:1.7}
.about-btn{left:78px;top:255px;width:170px;height:48px}
.mission-icon{left:630px}
.mission-title{left:685px;font-size:44px}
.mission-text{left:685px;width:470px;color:var(--white);font-size:15px;line-height:1.75}
.mission-text u{font-size:14px}
/* what we do */
.whatwedo{top:1465px;height:566px;background:linear-gradient(180deg,#262626,#151515)}
.whatwedo .title{top:60px;color:var(--white)}
.whatwedo .lead{left:130px;width:940px;top:130px;color:var(--white)}
.card-photo{position:absolute;top:217px;width:323px;height:189px}
.card-title{position:absolute;top:426px;width:323px;text-align:center;color:var(--white);font-family:"Roboto Condensed",sans-serif;font-size:23px}
.card-text{position:absolute;top:462px;width:323px;text-align:center;color:var(--white);font-size:15px;line-height:1.7}
.more{text-transform:uppercase;margin-left:6px}
/* different */
.different{top:2031px;height:527px;background:var(--white)}
.different .title{top:54px}
.different .lead{left:130px;width:940px;top:126px}
.diff-photo{position:absolute;top:215px;width:234px;height:135px}
.diff-title{position:absolute;top:374px;width:234px;text-align:center;color:var(--blue);font-family:"Roboto Condensed",sans-serif;font-size:22px;line-height:1.1}
.diff-text{position:absolute;width:234px;text-align:center;font-size:14.5px;line-height:1.7}
.diff-text .more{color:var(--blue)}
/* why */
.why{top:2558px;height:395px;background:linear-gradient(120deg,var(--orange) 0%,#f3a152 50%,var(--orange-dark) 100%)}
.why .title{top:54px;color:var(--white)}
.why .lead{left:200px;width:800px;top:120px;color:var(--white)}
.why-circle{position:absolute;top:217px;width:125px;height:125px;border-radius:50%;background:var(--white);display:flex;align-items:center;justify-content:center}
.why-title{position:absolute;top:232px;color:var(--white);font-family:"Roboto Condensed",sans-serif;font-size:23px}
.why-text{position:absolute;top:270px;width:320px;color:var(--white);font-size:15px;line-height:1.7}
/* contact */
.contact{top:2953px;height:531px;background:var(--light)}
.contact .title{top:50px}
.contact-name{left:78px;top:140px;color:var(--orange);font-weight:700;font-size:19px}
.info{position:absolute;display:flex;gap:16px;font-size:15px;line-height:1.75}
.map{left:78px;top:271px;width:498px;height:201px;background:linear-gradient(135deg,#ece7dc,#e3ddcf);border:1px solid var(--line)}
.field{position:absolute;left:621px;width:501px;background:var(--white);border:1px solid var(--line);font-size:14px;color:#999;padding:14px 18px}
.submit{left:999px;top:446px;width:123px;height:49px;font-size:18px}
/* footer */
.footer{top:3484px;height:59px;background:var(--orange)}
.footer-text{left:78px;top:19px;color:var(--white);font-size:14px}
.foot-dot{position:absolute;top:13px;width:33px;height:33px;border-radius:50%;background:var(--blue);border:2px solid var(--white)}
</style>
</head>
<body>

<div class="section topbar">
  <span class="social-dot" style="left:78px"></span>
  <span class="social-dot" style="left:108px"></span>
  <span class="social-dot" style="left:138px"></span>
  <div class="abs login">
    <svg width="12" height="13" viewBox="0 0 12 13" style="vertical-align:-1px;margin-right:6px"><rect x="1" y="5.5" width="10" height="7" rx="1" fill="#fff"/><path d="M3.5 5.5V4a2.5 2.5 0 0 1 5 0v1.5" stroke="#fff" stroke-width="1.6" fill="none"/></svg>Login
  </div>
</div>

<header class="section header">
  <div class="abs brand"><span class="brand-mark"></span><span class="brand-name">Tovarin Business Solution</span></div>
  <div class="abs call">Call us now</div>
  <div class="abs call-icon">
    <svg width="46" height="46" viewBox="0 0 46 46"><path d="M16 13l5 0 2 6-3 2a14 14 0 0 0 6 6l2-3 6 2v5a2 2 0 0 1-2 2A20 20 0 0 1 14 15a2 2 0 0 1 2-2z" fill="var(--orange)"/></svg>
  </div>
  <div class="abs call-number">123 555 0148</div>
</header>

<nav class="section nav">
  <ul>
    <li class="active">Home</li>
    <li>Who we are</li>
    <li>What we do</li>
    <li>What makes us different</li>
    <li>Why it matters</li>
    <li>Candidate portal</li>
    <li>Contact us</li>
  </ul>
</nav>

<section class="section hero">
  <div class="hero-photo" role="img" aria-label="Business team meeting around a desk with laptops and reports"></div>
  <h1 class="abs hero-title">TOVARIN</h1>
  <p class="abs hero-sub">Lorem Ipsum is simply dummy</p>
  <div class="abs btn-white hero-btn">Contact us now</div>
</section>

<section class="section welcome">
  <h2 class="abs title">Welcome to <span class="accent">Tovarin</span></h2>
  <p class="abs lead">Lorem Ipsum is simply dummy text of the printing and typesetting industry. Lorem Ipsum has been the industry's standard dummy text ever since the 1500s, when an unknown printer took a galley of type and scrambled it to make a type specimen book. It has survived not only five centuries, but also the leap into electronic typesetting, remaining essentially unchanged. It was popularised in the 1960s with the release of Letraset sheets containing Lorem Ipsum passages, and more recently with...</p>
  <div class="abs btn-blue welcome-btn">Read more <span>&#187;</span></div>
</section>

<section class="section about">
  <div class="abs about-left" role="img" aria-label="Orange tinted office photo"></div>
  <div class="abs about-right"></div>
  <div class="abs dash-v"></div>
  <div class="abs dash-h"></div>
  <h2 class="abs about-title">About Tovarin</h2>
  <p class="abs about-text">Lorem Ipsum is simply dummy text of the printing and typesetting industry. Lorem Ipsum has been the industry's standard dummy text ever since the 1500s, when an unknown printer took a galley of type and scrambled it to make a type specimen book. It has...</p>
  <div class="abs btn-white about-btn" style="font-weight:400">Read more&nbsp;<span>&#187;</span></div>

  <svg class="abs mission-icon" style="top:78px" width="40" height="40" viewBox="0 0 40 40"><circle cx="20" cy="20" r="16" stroke="#fff" stroke-width="3.5" fill="none"/><circle cx="20" cy="20" r="9" stroke="#fff" stroke-width="3.5" fill="none"/><circle cx="20" cy="20" r="3" fill="#fff"/></svg>
  <h2 class="abs mission-title" style="top:66px">Our Mission</h2>
  <p class="abs mission-text" style="top:120px">Lorem Ipsum is simply dummy text of the printing and type setting industry. Lorem Ipsum has been the... <u>READ MORE</u></p>
  <svg class="abs mission-icon" style="top:230px" width="42" height="36" viewBox="0 0 42 36"><path d="M4 26l26-14 4 8-26 14z" fill="#fff"/><rect x="32" y="6" width="8" height="14" rx="2" transform="rotate(-28 36 13)" fill="#fff"/></svg>
  <h2 class="abs mission-title" style="top:219px">Our Vision and Purpose</h2>
  <p class="abs mission-text" style="top:273px">Lorem Ipsum is simply dummy text of the printing and type setting industry. Lorem Ipsum has been the... <u>READ MORE</u></p>
</section>

<section class="section whatwedo">
  <h2 class="abs title">What we do</h2>
  <p class="abs lead">Lorem Ipsum is simply dummy text of the printing and typesetting industry. Lorem Ipsum has been the industry's standard dummy text ever since the 1500s.</p>

  <div class="card-photo" style="left:78px;background:linear-gradient(135deg,#c9d3de,#7f8fa1)" role="img" aria-label="Recruiter interviewing a candidate at a laptop"></div>
  <h3 class="card-title" style="left:78px">IT Recruiting</h3>
  <p class="card-text" style="left:78px">Lorem Ipsum is simply dummy text of the printing and typesetting industry. Lorem Ipsum has...<span class="more">Read more &#187;</span></p>

  <div class="card-photo" style="left:439px;background:linear-gradient(135deg,#e2e2e4,#9a9ca4)" role="img" aria-label="Trainer presenting to a group in a meeting room"></div>
  <h3 class="card-title" style="left:439px">IT Training</h3>
  <p class="card-text" style="left:439px">Lorem Ipsum is simply dummy text of the printing and typesetting industry. Lorem Ipsum has...<span class="more">Read more &#187;</span></p>

  <div class="card-photo" style="left:799px;background:linear-gradient(135deg,#d9b38c,#6b4427)" role="img" aria-label="Laptop on a wooden desk"></div>
  <h3 class="card-title" style="left:799px">Hardware and software sales</h3>
  <p class="card-text" style="left:799px">Lorem Ipsum is simply dummy text of the printing and typesetting industry. Lorem Ipsum has...<span class="more">Read more &#187;</span></p>
</section>

<section class="section different">
  <h2 class="abs title">What makes us <span class="accent">different</span></h2>
  <p class="abs lead">Lorem Ipsum is simply dummy text of the printing and typesetting industry. Lorem Ipsum has been the industry's standard dummy text ever since the 1500s.</p>

  <div class="diff-photo" style="left:78px;background:linear-gradient(135deg,#cdd9e6,#8096ad)" role="img" aria-label="Colleagues working together at a table"></div>
  <h3 class="diff-title" style="left:78px">We Live What We Do</h3>
  <p class="diff-text" style="left:78px;top:410px">Lorem Ipsum is simply dummy text of the printing and typeset industry...<span class="more">Read more &#187;</span></p>

  <div class="diff-photo" style="left:350px;background:linear-gradient(135deg,#d8d4cc,#6d6a66)" role="img" aria-label="Hands reviewing documents on a desk"></div>
  <h3 class="diff-title" style="left:350px">We Don't Compromise Quality</h3>
  <p class="diff-text" style="left:350px;top:430px">Lorem Ipsum is simply dummy text of the printing and types...<span class="more">Read more &#187;</span></p>

  <div class="diff-photo" style="left:619px;background:linear-gradient(135deg,#eceef0,#a8adb5)" role="img" aria-label="Team discussing charts on a whiteboard"></div>
  <h3 class="diff-title" style="left:619px">We Share Knowledge</h3>
  <p class="diff-text" style="left:619px;top:410px">Lorem Ipsum is simply dummy text of the printing and typeset industry...<span class="more">Read more &#187;</span></p>

  <div class="diff-photo" style="left:888px;background:linear-gradient(135deg,#b8c6d6,#3f5670)" role="img" aria-label="Business handshake"></div>
  <h3 class="diff-title" style="left:888px">Staffing Guarantee</h3>
  <p class="diff-text" style="left:888px;top:410px">Lorem Ipsum is simply dummy text of the printing and typeset industry...<span class="more">Read more &#187;</span></p>
</section>

<section class="section why" role="img" aria-label="Orange tinted photo of a business team">
  <h2 class="abs title">Why it matters</h2>
  <p class="abs lead">Lorem Ipsum is simply dummy text of the printing and typesetting industry.<br>Lorem Ipsum has a been the industry's standard.</p>

  <div class="why-circle" style="left:130px">
    <svg width="56" height="60" viewBox="0 0 56 60"><path d="M14 4h22l10 10v42H14z" fill="var(--blue)"/><path d="M36 4v10h10" fill="#5b8fc8"/><circle cx="16" cy="38" r="8" fill="var(--blue)" stroke="#fff" stroke-width="2"/><path d="M2 58a14 12 0 0 1 28 0z" fill="var(--blue)" stroke="#fff" stroke-width="2"/></svg>
  </div>
  <h3 class="why-title" style="left:283px">Quickly Fill Positions</h3>
  <p class="why-text" style="left:283px">Lorem Ipsum is simply dummy text of the printing and typesetting industry. Lorem Ipsum has...<span class="more">Read more &#187;</span></p>

  <div class="why-circle" style="left:626px">
    <svg width="60" height="56" viewBox="0 0 60 56"><path d="M4 52h16v-10h14v-10h14v-10h8v30z" fill="var(--blue)"/><path d="M14 34l10-12 8 4 8-14" stroke="var(--blue)" stroke-width="4" fill="none" stroke-linecap="round"/><path d="M34 10l8 0 0 8" stroke="var(--blue)" stroke-width="4" fill="none"/></svg>
  </div>
  <h3 class="why-title" style="left:780px">Candidate Career Development</h3>
  <p class="why-text" style="left:780px">Lorem Ipsum is simply dummy text of the printing and typesetting industry. Lorem Ipsum has...<span class="more">Read more &#187;</span></p>
</section>

<section class="section contact">
  <h2 class="abs title">Contact <span class="accent">us</span></h2>
  <div class="abs contact-name">TOVARIN</div>
  <div class="info" style="left:78px;top:174px">
    <svg width="14" height="20" viewBox="0 0 14 20" style="margin-top:4px"><path d="M7 0a7 7 0 0 1 7 7c0 5-7 13-7 13S0 12 0 7a7 7 0 0 1 7-7z" fill="var(--blue)"/><circle cx="7" cy="7" r="2.6" fill="#fff"/></svg>
    <span style="width:230px">Lorem Ipsum is simply dummy text of the printing.</span>
  </div>
  <div class="info" style="left:390px;top:160px">
    <svg width="18" height="18" viewBox="0 0 18 18" style="margin-top:5px"><path d="M3 1h4l1.5 4.5-2.3 1.5a10 10 0 0 0 4.8 4.8l1.5-2.3L17 11v4a2 2 0 0 1-2 2A15 15 0 0 1 1 3a2 2 0 0 1 2-2z" fill="var(--blue)"/></svg>
    <span>(123) 555 - 0148</span>
  </div>
  <div class="info" style="left:390px;top:197px">
    <svg width="18" height="14" viewBox="0 0 18 14" style="margin-top:6px"><rect width="18" height="14" rx="1" fill="var(--blue)"/><path d="M1 1l8 7 8-7" stroke="#fff" stroke-width="1.6" fill="none"/></svg>
    <span>Lorem Ipsum simply</span>
  </div>
  <div class="abs map" role="img" aria-label="Street map showing the office location"></div>

  <div class="field" style="top:136px;height:52px">Name</div>
  <div class="field" style="top:200px;height:50px">Email</div>
  <div class="field" style="top:262px;height:49px">Subject</div>
  <div class="field" style="top:321px;height:101px">Message</div>
  <div class="abs btn-blue submit">Submit</div>
</section>

<footer class="section footer">
  <div class="abs footer-text">&copy; TOVARIN BUSINESS SOLUTION LLC - 2016. All Rights Reserved</div>
  <span class="foot-dot" style="left:988px"></span>
  <span class="foot-dot" style="left:1035px"></span>
  <span class="foot-dot" style="left:1084px"></span>
</footer>

</body>
</html>
```